a business advisory consulting website

I need a website 3-5 pages to sell my professional services in IT and Project management Consulting. My company name is Crestline Advisory Consulting. I want it to be device friendly and easy to navigate for the busy executive however intriguing enough.
I have attached some info I drafted on About the company and personal Bio. Also there is a website that I really like that I have attached the initial site pdf and websites that I like are here: https://tollmeradvisors.example, https://quarvelanalytics.example, https://www.dorvikstudylearning.example as examples. Thanks
Updates

Hi Designers, I have uploaded the logo in 3D .png format, to assist in the web design.

Target Market(s)

B2B, governments, IT companies, Project Management companies and Consulting firms, small medium enterprises to large corporate enterprises.

Industry/Entity Type

It Professional

Coding

Coded - Design and coding required

Number of Pages Required

5+ page

Font styles to use
Sans Serif

Requirements
Must have
• Home, About company, the team, what we do and contact us
Nice to have
• Blog
Should not have
• pop ups, flash

```html
<!DOCTYPE html>
<html lang="en">
<head>
<meta charset="utf-8">
<title>Crestline Advisory — Home</title>
<link rel="stylesheet" href="https://fonts.googleapis.com/css2?family=Zilla+Slab:wght@300;400;600;700&family=Lato:wght@400;700&display=swap">
<style>
:root{
  --navy:#1f2140;
  --navy-deep:#1b1d3a;
  --red:#d7101f;
  --ink:#2a2a36;
  --white:#ffffff;
  --footer:#e8e8eb;
  --slab:"Zilla Slab", Georgia, serif;
  --sans:"Lato", Arial, sans-serif;
}
*{box-sizing:border-box;margin:0;padding:0}
html,body{width:1200px;height:3336px;overflow:hidden}
body{position:relative;background:var(--white);font-family:var(--sans);color:var(--ink)}
.abs{position:absolute}
.shapes{position:absolute;left:0;top:0;z-index:1}
.layer{z-index:2}
.btn{position:absolute;z-index:3;background:var(--red);color:var(--white);font-family:var(--slab);font-weight:700;font-size:15px;display:flex;align-items:center;justify-content:center;letter-spacing:.3px}

/* header */
.brand{left:144px;top:30px;display:flex;align-items:center;gap:10px;z-index:3}
.brand-mark{width:36px;height:36px;background:var(--red)}
.brand-name{font-family:var(--slab);font-weight:700;font-size:27px;line-height:1;color:var(--navy)}
.nav{left:494px;top:40px;display:flex;gap:32px;z-index:3;font-family:var(--slab);font-weight:600;font-size:17px;color:var(--navy)}
.nav .active{color:var(--red)}

/* hero */
.hero-photo{left:0;top:119px;width:1200px;height:630px;z-index:0;background:linear-gradient(100deg,#6d6055 0%,#9c8e80 35%,#c9c7c3 65%,#e3e2df 100%)}
.hero-title{left:300px;width:600px;top:284px;text-align:center;z-index:3;font-family:var(--slab);font-weight:600;font-size:38px;line-height:48px;color:var(--navy)}
.slide-arrow{width:40px;height:40px;background:var(--navy);transform:rotate(45deg);z-index:3;display:flex;align-items:center;justify-content:center}
.slide-arrow svg{transform:rotate(-45deg)}

/* welcome */
.welcome h1{font-family:var(--slab);font-weight:700;font-size:39px;color:var(--navy);line-height:1}
.welcome{left:144px;top:818px;width:520px;z-index:3}
.welcome p{font-size:13.5px;line-height:25.6px;margin-top:26px;color:var(--ink)}
.welcome h1+p{margin-top:22px}
.welcome-back{left:700px;top:818px;width:354px;height:290px;background:var(--navy);transform:rotate(2deg);z-index:2}
.welcome-photo{left:692px;top:828px;width:352px;height:270px;background:linear-gradient(120deg,#5e6b74,#a5afb4 45%,#7b7f80);z-index:3}

/* services */
.section-title{position:absolute;left:0;width:1200px;text-align:center;z-index:3;font-family:var(--slab);font-weight:700;font-size:38px}
.service{top:1470px;width:390px;z-index:3;color:var(--white)}
.service h3{font-family:var(--slab);font-weight:300;font-size:30px;line-height:40px;text-transform:uppercase;margin-top:22px}
.service p{font-size:12px;line-height:24px;margin-top:6px}
.divider{left:598px;top:1460px;width:1px;height:375px;background:rgba(255,255,255,.6);z-index:3}

/* team */
.team-photo{left:144px;top:2175px;width:290px;height:460px;z-index:3;background:linear-gradient(180deg,#f2f2f2,#2b2b33 55%,#15151c);border-radius:120px 120px 0 0}
.member{left:487px;top:2192px;width:570px;z-index:3}
.member h2{font-family:var(--slab);font-weight:300;font-size:32px;color:var(--red)}
.member p{font-size:13.5px;line-height:25.6px;margin-top:18px}
.member h2+p{margin-top:16px}

/* contact */
.info{left:144px;z-index:3;display:flex;align-items:center;gap:14px;color:var(--white);font-family:var(--slab)}
.info .dot{width:40px;height:40px;border-radius:50%;background:var(--white);display:flex;align-items:center;justify-content:center}
.field{position:absolute;z-index:3;background:var(--white);font-size:13px;color:#555;padding:11px 14px}

/* footer */
.foot-links{left:144px;top:3251px;font-size:11.5px;color:var(--navy);z-index:3}
.foot-links span{margin:0 8px}
.copyright{left:144px;top:3283px;font-size:11.5px;color:var(--navy);z-index:3}
.social{top:3254px;width:44px;height:44px;border-radius:50%;border:1.5px solid var(--navy);z-index:3}
</style>
</head>
<body>

<div class="abs hero-photo" role="img" aria-label="Photo: two businessmen shaking hands across a meeting table"></div>

<svg class="shapes" width="1200" height="3336" viewBox="0 0 1200 3336" aria-hidden="true">
  <!-- hero edge -->
  <polygon points="0,742 1055,613 1200,716 1200,760 0,760" fill="#d7101f"/>
  <polygon points="0,749 1055,630 1200,738 1200,770 0,770" fill="#ffffff"/>
  <!-- services band -->
  <defs>
    <linearGradient id="navyBand" x1="0" y1="0" x2="1" y2="1">
      <stop offset="0" stop-color="#252849"/><stop offset="1" stop-color="#1b1d3a"/>
    </linearGradient>
  </defs>
  <polygon points="0,1303 1055,1189 1200,1290 1200,2040 0,2040" fill="url(#navyBand)"/>
  <polygon points="0,2036 1055,1910 1200,2014 1200,2060 0,2060" fill="#d7101f"/>
  <polygon points="0,2044 1055,1928 1200,2035 1200,2070 0,2070" fill="#ffffff"/>
  <!-- contact band -->
  <polygon points="0,2650 1055,2537 1200,2640 1200,3240 0,3240" fill="url(#navyBand)"/>
  <polygon points="0,3231 1055,3105 1200,3208 1200,3250 0,3250" fill="#d7101f"/>
  <polygon points="0,3238 1055,3124 1200,3230 1200,3336 0,3336" fill="#e8e8eb"/>
</svg>

<!-- header -->
<div class="abs brand"><span class="brand-mark"></span><span class="brand-name">CRESTLINE<br>ADVISORY</span></div>
<nav class="abs nav"><span class="active">Home</span><span>About Company</span><span>What We Do</span><span>The Team</span><span>Contact Us</span></nav>

<!-- hero -->
<div class="abs slide-arrow" style="left:54px;top:346px"><svg width="16" height="16" viewBox="0 0 16 16"><path d="M10 2 4 8l6 6" fill="none" stroke="#fff" stroke-width="3"/></svg></div>
<div class="abs slide-arrow" style="left:1106px;top:346px"><svg width="16" height="16" viewBox="0 0 16 16"><path d="M6 2l6 6-6 6" fill="none" stroke="#fff" stroke-width="3"/></svg></div>
<h2 class="abs hero-title">Proin eget congue nulla vel tempor diam</h2>
<div class="btn" style="left:532px;top:393px;width:136px;height:47px">CONTACT US</div>

<!-- welcome -->
<section class="abs welcome">
  <h1>Welcome to Crestline Advisory</h1>
  <p>We are a specialist operational excellence firm, delivering consulting and advisory services in six core capabilities, across all industries and all business lines to improve performance, efficiency, profitability, automation and scalability, for clients across Australia.</p>
  <p>We’re known for our pragmatism, in depth analysis, strategic insight and nurturing long-term client self-sufficiency. We approach business consulting differently, with a Genuine Client Partnership model that builds client capability and rightsized solutions for the client.</p>
</section>
<div class="abs welcome-back"></div>
<div class="abs welcome-photo" role="img" aria-label="Photo: colleagues discussing ideas around an office table"></div>

<!-- what we do -->
<h2 class="section-title" style="top:1380px;color:#fff">What We Do</h2>
<div class="abs divider"></div>
<article class="abs service" style="left:144px">
  <svg width="62" height="62" viewBox="0 0 62 62" fill="none" stroke="#fff" stroke-width="2">
    <circle cx="22" cy="22" r="12"/><circle cx="22" cy="22" r="5"/>
    <circle cx="42" cy="42" r="11"/><circle cx="42" cy="42" r="4"/>
    <path d="M22 4v6M22 34v6M4 22h6M34 22h6M42 25v5M42 54v5M25 42h5M54 42h5"/>
  </svg>
  <h3>Process Improvement within Government</h3>
  <p>Across the three levels of Government – Federal, State/Territory and Local – leaders continually face complex decisions around how to allocate limited resources to best service their citizens. In the past, Governments have faced criticism for an over reliance on bureaucracy and an inability to adapt or even prepare for the future.</p>
</article>
<div class="btn" style="left:144px;top:1776px;width:136px;height:47px">READ MORE</div>
<article class="abs service" style="left:681px">
  <svg width="62" height="62" viewBox="0 0 62 62" fill="none" stroke="#fff" stroke-width="2">
    <rect x="6" y="8" width="42" height="52"/><path d="M12 8V3h42v52h-6"/>
    <circle cx="26" cy="30" r="10"/><path d="M26 20v10h10M14 48h26M14 54h18"/>
  </svg>
  <h3>Technology Analysis within Healthcare</h3>
  <p>Australia’s healthcare system is a complex web of public and private providers, settings, participants and supporting mechanisms. Health providers include medical practitioners, nurses, allied and other health professionals, hospitals, clinics and government agencies and private providers.</p>
</article>
<div class="btn" style="left:681px;top:1776px;width:136px;height:47px">READ MORE</div>

<!-- team -->
<h2 class="section-title" style="top:2108px;color:var(--navy)">Team</h2>
<svg class="abs layer" style="left:52px;top:2392px" width="24" height="32" viewBox="0 0 24 32"><path d="M18 3 6 16l12 13" fill="none" stroke="#1f2140" stroke-width="3"/></svg>
<svg class="abs layer" style="left:1122px;top:2392px" width="24" height="32" viewBox="0 0 24 32"><path d="M6 3l12 13-12 13" fill="none" stroke="#1f2140" stroke-width="3"/></svg>
<div class="abs team-photo" role="img" aria-label="Photo: team member in a dark suit with arms crossed"></div>
<section class="abs member">
  <h2>Marcus Ellery</h2>
  <p>Marcus Ellery is an IT professional with more than 20 years of experience turning business initiatives into technology solutions. His expertise has been identifying deficiencies and developing or facilitating the best solutions for an outcome that is satisfactory to all stakeholders involved.</p>
  <p>Marcus improves business processes as older organizations restructure or migrate to newer technologies. He bridges the gap between the actual people in these organizations transitioning and the new technologies they seek which is a value add to any organization's success.</p>
</section>
<div class="btn" style="left:487px;top:2473px;width:136px;height:47px">READ MORE</div>

<!-- contact -->
<h2 class="section-title" style="top:2728px;color:#fff">Contact Us</h2>
<div class="abs info" style="top:2803px;font-size:17px">
  <span class="dot"><svg width="16" height="18" viewBox="0 0 16 18"><path d="M8 1a6 6 0 0 0-6 6c0 5 6 10 6 10s6-5 6-10a6 6 0 0 0-6-6z" fill="#d7101f"/><circle cx="8" cy="7" r="2" fill="#fff"/></svg></span>24 Building name, Street name, City Zipcode</div>
<div class="abs info" style="top:2866px;font-size:26px;font-weight:600">
  <span class="dot"><svg width="16" height="16" viewBox="0 0 16 16"><path d="M3 1l3 3-2 2c1 2 3 4 5 5l2-2 3 3-2 3C7 15 1 9 1 3z" fill="#d7101f"/></svg></span>555 014 2287</div>
<div class="abs info" style="top:2929px;font-size:26px;font-weight:600">
  <span class="dot"><svg width="16" height="12" viewBox="0 0 16 12"><rect width="16" height="12" rx="1" fill="#d7101f"/><path d="M1 1l7 6 7-6" fill="none" stroke="#fff" stroke-width="1.5"/></svg></span>info@crestline.example</div>

<div class="field" style="left:617px;top:2805px;width:214px;height:40px">Name</div>
<div class="field" style="left:841px;top:2805px;width:215px;height:40px">Company Name</div>
<div class="field" style="left:617px;top:2855px;width:214px;height:40px">Email</div>
<div class="field" style="left:841px;top:2855px;width:215px;height:40px">Phone</div>
<div class="field" style="left:617px;top:2905px;width:439px;height:62px">Message</div>
<div class="btn" style="left:617px;top:2977px;width:104px;height:47px">SUBMIT</div>

<!-- footer -->
<div class="abs foot-links">Home<span>|</span>About Company<span>|</span>What We Do<span>|</span>The Team<span>|</span>Contact Us</div>
<div class="abs copyright">Copyright © 2020 &nbsp; Crestline Advisory. &nbsp; All rights reserved.</div>
<div class="abs social" style="left:947px"></div>
<div class="abs social" style="left:1011px"></div>

</body>
</html>
```